BrivoTerna. Lantern of the Steady Harvest. Business card

Professional business card for BrivoTerna (Lantern of the Steady Harvest)
My rationale: Strategy-> Execution-> Results-> Value that lead to the BrivoTerna name: We put the Lantern of the Steady Harvest.
We deliver value to our customers helping them at defining a good strategy (cyan arrow). 90% of well formulated strategies fail due to poor execution so we also consider strategical execution very important (green arrow). Due to the execution we obtain the results (blue arrow). Finally, the results provide feedback to redefine strategy, and the new strategy has to be executed and new results obtained providing new feedback and on and on. It's like a wheel that finally, must create corporate value: value for shareholders, staholders, employees, providers...-

Target Market(s)

CEOs and steering comitees , invewrnent funds

Industry/Entity Type

Business Consultant

Contact Information for Business Card

Teodoro Vinsquel
CEO & Founder
teodoro.vinsquel@brivoterna-example.com
Mobile: +34 655.803.912
www.brivoterna-example.com

Colors

Designer to choose colors to be used in the design.

Requirements
Nice to have
• Nice to hace the words: Strategy, execution, results
• Nice to vave the claim: Lantern of the Steady Harvest
• The three colors should be shown:
• cyan for STRATEGY
• green for EXECUTION
• blue for RESULTS
Should not have
• Complete black background

```html
<!DOCTYPE html>
<html lang="en">
<head>
<meta charset="utf-8">
<title>BrivoTerna business card</title>
<link href="https://fonts.googleapis.com/css2?family=Open+Sans:wght@400;600;700&display=swap" rel="stylesheet">
<style>
  :root {
    --stage: #2d2d2f;
    --navy: #243b8c;
    --navy-text: #233a8e;
    --green: #8cc63f;
    --cyan: #29a9e0;
    --white: #ffffff;
    --ink: #2a2a2a;
  }
  * { margin: 0; padding: 0; box-sizing: border-box; }
  html, body {
    width: 1200px; height: 900px; overflow: hidden;
    background: var(--stage);
    font-family: "Open Sans", Arial, sans-serif;
  }
  .stage {
    width: 1200px; height: 900px;
    display: flex; flex-direction: column;
    align-items: center; justify-content: center; gap: 44px;
  }
  .card {
    position: relative;
    width: 660px; height: 377px;
    box-shadow: 0 14px 30px rgba(0,0,0,.45);
  }

  /* Front */
  .card--front { background: var(--navy); color: var(--white); }
  .brand-front {
    position: absolute; left: 0; right: 0; top: 118px;
    display: flex; align-items: center; justify-content: center; gap: 16px;
  }
  .brand-dot { width: 22px; height: 22px; border-radius: 50%; background: var(--green); }
  .brand-front .brand-name {
    font-size: 60px; font-weight: 700; letter-spacing: -1px; color: var(--white);
  }
  .front-rule {
    position: absolute; left: 40px; right: 40px; top: 280px;
    height: 2px; background: var(--green);
  }
  .pillars {
    position: absolute; left: 40px; right: 40px; top: 300px;
    display: flex; justify-content: space-between;
    font-size: 19px; font-weight: 700; letter-spacing: .5px;
  }
  .pillar--strategy { color: var(--white); }
  .pillar--execution { color: var(--green); margin-top: 24px; }
  .pillar--results { color: var(--cyan); margin-top: 48px; }

  /* Back */
  .card--back { background: var(--white); color: var(--ink); }
  .holder { position: absolute; left: 44px; top: 40px; }
  .holder-name {
    font-size: 27px; font-weight: 700; color: var(--navy-text);
    letter-spacing: 1px; text-transform: uppercase; line-height: 1.1;
  }
  .holder-role { font-size: 17px; color: var(--green); margin-top: 2px; }
  .contacts { list-style: none; margin-top: 12px; }
  .contacts li {
    display: flex; align-items: center; gap: 12px;
    font-size: 17px; line-height: 30px; color: var(--ink);
  }
  .contacts svg { width: 20px; height: 20px; flex: none; }
  .back-rule {
    position: absolute; left: 44px; right: 44px; top: 244px;
    height: 2px; background: var(--green);
  }
  .claim {
    position: absolute; left: 44px; top: 262px;
    font-size: 18px; text-transform: uppercase; letter-spacing: .5px; color: var(--ink);
  }
  .brand-back {
    position: absolute; right: 44px; top: 176px;
    display: flex; align-items: center; gap: 12px;
  }
  .brand-back .brand-dot { width: 18px; height: 18px; }
  .brand-back .brand-name {
    font-size: 44px; font-weight: 700; letter-spacing: -1px; color: var(--navy-text);
  }
</style>
</head>
<body>
<main class="stage">
  <section class="card card--front">
    <div class="brand-front">
      <span class="brand-dot"></span>
      <span class="brand-name">BrivoTerna</span>
    </div>
    <div class="front-rule"></div>
    <div class="pillars">
      <span class="pillar pillar--strategy">STRATEGY</span>
      <span class="pillar pillar--execution">EXECUTION</span>
      <span class="pillar pillar--results">RESULTS</span>
    </div>
  </section>

  <section class="card card--back">
    <div class="holder">
      <h1 class="holder-name">Teodoro Vinsquel</h1>
      <p class="holder-role">CEO &amp; Founder</p>
      <ul class="contacts">
        <li>
          <svg viewBox="0 0 24 24" fill="none" stroke="#29a9e0" stroke-width="1.6"><circle cx="12" cy="12" r="10"/><path d="M8.5 7.5c-.6.6-.6 2 .6 3.9 1.3 2 3 3.6 4.6 4.3 1.2.5 2 .4 2.5-.2l.6-.8-2-1.6-1.1.8c-1-.5-2.3-1.8-2.9-2.9l.8-1.1-1.6-2z"/></svg>
          +34 655.803.912
        </li>
        <li>
          <svg viewBox="0 0 24 24" fill="none" stroke="#243b8c" stroke-width="1.6"><rect x="3" y="6" width="18" height="12" rx="1"/><path d="M3 6l9 7 9-7"/></svg>
          teodoro.vinsquel@brivoterna-example.com
        </li>
        <li>
          <svg viewBox="0 0 24 24" fill="none" stroke="#29a9e0" stroke-width="1.6"><circle cx="12" cy="12" r="9"/><ellipse cx="12" cy="12" rx="4" ry="9"/><path d="M3 12h18M5 7h14M5 17h14"/></svg>
          www.brivoterna-example.com
        </li>
      </ul>
    </div>
    <div class="brand-back">
      <span class="brand-dot"></span>
      <span class="brand-name">BrivoTerna</span>
    </div>
    <div class="back-rule"></div>
    <p class="claim">Lantern of the Steady Harvest</p>
  </section>
</main>
</body>
</html>
```